Real Estate Development requires a tri-fold corporate brochure

I need a clean, elegant, Corporate tri-fold brochure for a real estate development. Currently operation in Dubai, we plan to enter European markets and will hand out the brochures to potential, future cooperation partners. A color combination in line with our logo would be great. The overall design should communicate that we are holding numerous high-end properties in Dubai and London and our financial strength.

Target Market(s)

Europe

Industry/Entity Type

Real Estate Development

Contact Information for Business Card

Lorin Vasquel, MBA
Senior Business Development Manager
Marble Crest UAE
Cell UAE: +971 56 482 9153
Cell Austria: +43 650 317 8826
lova@marblecrest.ae

Requirements
Must have
• Clean, corporate design, not too colorful, a few nice pictures of existing real estate properties. See the attached pdf-document for more details.
Nice to have
• Refurbished logo

```html
<!DOCTYPE html>
<html lang="en">
<head>
<meta charset="utf-8">
<title>Marble Crest – Tri-fold Brochure Panels</title>
<link rel="stylesheet" href="https://fonts.googleapis.com/css2?family=Cinzel:wght@400;700&family=Lato:wght@400;700&display=swap">
<style>
  :root {
    --backdrop: #c9d1dc;
    --navy-deep: #0a2159;
    --navy: #123a86;
    --lime: #c6df1c;
    --white: #ffffff;
    --muted: #d6def0;
    --photo-warm: #e9d6b8;
    --photo-mid: #8a7a66;
    --photo-dark: #3a3430;
  }
  * { margin: 0; padding: 0; box-sizing: border-box; }
  html, body {
    width: 1200px; height: 900px; overflow: hidden;
    background: var(--backdrop);
  }
  .spread {
    position: relative; width: 1200px; height: 900px;
    display: flex; justify-content: center; align-items: center; gap: 60px;
  }
  .panel {
    width: 360px; height: 780px;
    display: flex; flex-direction: column;
    box-shadow: 0 6px 18px rgba(20, 30, 60, 0.25);
    background: var(--navy-deep);
  }
  .band {
    background: radial-gradient(ellipse at 50% 30%, var(--navy) 0%, var(--navy-deep) 85%);
    color: var(--white);
  }
  .photo {
    flex: none;
    background: linear-gradient(120deg, var(--photo-warm) 0%, #cdb392 35%, var(--photo-mid) 65%, var(--photo-dark) 100%);
  }

  /* Front cover */
  .cover-head { height: 130px; display: flex; align-items: center; justify-content: center; }
  .brand-name {
    font-family: "Lato", sans-serif; font-weight: 700; font-size: 24px;
    letter-spacing: 1px; color: var(--white);
  }
  .cover-photo { height: 420px; }
  .cover-foot {
    flex: 1; display: flex; flex-direction: column; justify-content: center;
    padding-left: 44px; padding-bottom: 40px;
  }
  .headline {
    font-family: "Cinzel", serif; font-weight: 700; font-size: 27px;
    letter-spacing: 6px; line-height: 1.45; text-transform: uppercase;
  }
  .headline .accent { color: var(--lime); display: block; }
  .headline .plain { color: var(--white); display: block; }

  /* Back panel */
  .back-head { height: 130px; display: flex; align-items: center; padding: 0 38px; }
  .intro {
    font-family: "Lato", sans-serif; font-size: 10.5px; line-height: 1.65;
    color: var(--muted); text-align: center;
  }
  .back-photo { height: 420px; }
  .back-foot { flex: 1; padding: 30px 38px; font-family: "Lato", sans-serif; }
  .contact-name { color: var(--lime); font-weight: 700; font-size: 12px; letter-spacing: 1px; text-transform: uppercase; }
  .contact-role { color: var(--lime); font-weight: 700; font-size: 10px; letter-spacing: 1px; text-transform: uppercase; margin-top: 4px; }
  .contact-company { color: var(--white); font-size: 10.5px; margin-top: 10px; }
  .contact-list { list-style: none; margin-top: 8px; }
  .contact-list li { color: var(--muted); font-size: 10.5px; line-height: 1.8; display: flex; align-items: center; gap: 8px; }
  .contact-list svg { width: 11px; height: 11px; flex: none; }
</style>
</head>
<body>
<main class="spread">
  <section class="panel panel--back">
    <header class="band back-head">
      <p class="intro">We develop and hold premium residential and commercial properties in Dubai and London. Our long-term capital base allows us to act with confidence and build lasting partnerships with investors across Europe who share our values of quality.</p>
    </header>
    <div class="photo back-photo" role="img" aria-label="Business team meeting in a sunlit high-rise office with window blinds"></div>
    <footer class="band back-foot">
      <p class="contact-name">Lorin Vasquel, MBA</p>
      <p class="contact-role">Senior Business Development Manager</p>
      <p class="contact-company">Marble Crest UAE</p>
      <ul class="contact-list">
        <li><svg viewBox="0 0 12 12"><path d="M3 1l2 2-1 1.5a7 7 0 0 0 3.5 3.5L9 7l2 2-1.5 2A9 9 0 0 1 1 2.5z" fill="#c6df1c"/></svg>UAE: +971 56 482 9153</li>
        <li><svg viewBox="0 0 12 12"><path d="M3 1l2 2-1 1.5a7 7 0 0 0 3.5 3.5L9 7l2 2-1.5 2A9 9 0 0 1 1 2.5z" fill="#c6df1c"/></svg>Austria: +43 650 317 8826</li>
        <li><svg viewBox="0 0 12 12"><rect x="1" y="2.5" width="10" height="7" fill="none" stroke="#c6df1c" stroke-width="1.2"/><path d="M1 3l5 4 5-4" fill="none" stroke="#c6df1c" stroke-width="1.2"/></svg>lova@marblecrest.ae</li>
        <li><svg viewBox="0 0 12 12"><circle cx="6" cy="6" r="4.8" fill="none" stroke="#c6df1c" stroke-width="1.2"/><path d="M1.2 6h9.6M6 1.2c2 2.5 2 7 0 9.6M6 1.2c-2 2.5-2 7 0 9.6" fill="none" stroke="#c6df1c" stroke-width="1"/></svg>marblecrest.ae</li>
      </ul>
    </footer>
  </section>

  <section class="panel panel--cover">
    <header class="band cover-head">
      <span class="brand-name">Marble Crest</span>
    </header>
    <div class="photo cover-photo" role="img" aria-label="Silhouetted business people discussing documents by large office windows at sunset"></div>
    <footer class="band cover-foot">
      <h1 class="headline">
        <span class="accent">Real-Estate</span>
        <span class="plain">Competence</span>
      </h1>
    </footer>
  </section>
</main>
</body>
</html>
```